Zestora - Landing Page

Need a landing page for a journal app. The app is based on a retrospective board, where each journal entry is split into 3 sections: "What went well", "What Didn't Go Well" and "Things To Try".
The landing page should match the style of all modern web application landing pages. Think Brint, Tivalo, Mirvane. I've included screenshots of the app.
One feature that I want to highlight that is not ready yet, is an AI coach. It will offer insights based on the history of the user's journal entries
1 page

```html
<!DOCTYPE html>
<html lang="en">
<head>
<meta charset="utf-8">
<title>Zestora – Journal App</title>
<link href="https://fonts.googleapis.com/css2?family=Rubik:wght@500;600;700;800&family=Inter:wght@400;500;600;700&display=swap" rel="stylesheet">
<style>
:root{
  --ink:#16181d;
  --text:#3a3f48;
  --muted:#6b7280;
  --blue:#1460c9;
  --blue-soft:#9bbde6;
  --bg:#f3f6fa;
  --hero:#e6eef8;
  --band:#e3ecf7;
  --card:#ffffff;
  --green:#22a565;
  --orange:#f5a31a;
  --navy:#1c2536;
  --line:#d5dce6;
}
*{margin:0;padding:0;box-sizing:border-box}
html,body{width:1200px;height:3595px;overflow:hidden}
body{background:var(--bg);font-family:"Inter",sans-serif;color:var(--text);position:relative}
.abs{position:absolute}
h1,h2,h3{font-family:"Rubik",sans-serif;color:var(--ink)}

/* hero */
.hero{position:absolute;left:0;top:0;width:1200px;height:675px;background:linear-gradient(180deg,#e9f0f9 0%,#e4edf8 70%,#eaf1f9 100%);overflow:hidden}
.hero .glow{position:absolute;border-radius:50%;filter:blur(40px)}
.nav-logo{left:95px;top:20px;display:flex;align-items:center;gap:10px;font-family:"Rubik",sans-serif;font-weight:700;font-size:21px;color:var(--ink)}
.logo-dot{width:18px;height:18px;border-radius:50%;background:var(--orange)}
.nav-links{left:453px;top:22px;display:flex;gap:18px;font-size:14px;color:var(--ink)}
.nav-links span.sep{color:var(--ink)}
.btn-outline{left:975px;top:14px;width:111px;height:34px;border:1.5px solid var(--blue);border-radius:17px;font-size:11px;color:var(--blue);display:flex;align-items:center;justify-content:center;background:#fff}
.hero-kicker{left:0;width:1200px;top:122px;text-align:center;font-size:24px;color:var(--ink)}
.hero-title{left:0;width:1200px;top:162px;text-align:center;font-size:44px;line-height:52px;font-weight:700}
.hero-title .hl{color:var(--blue)}
.hero-sub{left:0;width:1200px;top:287px;text-align:center;font-size:15.5px;line-height:18px;color:var(--ink)}
.btn-dark{left:486px;top:344px;width:221px;height:50px;border-radius:25px;background:var(--navy);color:#fff;font-size:14px;font-weight:600;display:flex;align-items:center;justify-content:center;gap:8px}
.avatar{position:absolute;border-radius:50%;border:3px solid #fff;box-shadow:0 4px 12px rgba(30,50,90,.15)}

/* laptop */
.laptop-screen{left:373px;top:455px;width:447px;height:298px;background:#1b1d22;border-radius:14px;padding:12px}
.app{width:100%;height:100%;background:#fff;display:flex;border-radius:2px;overflow:hidden}
.app-bar{width:14px;background:var(--navy)}
.app-main{flex:1;padding:8px 10px;position:relative}
.app-top{height:12px;background:#eef1f5;margin:-8px -10px 6px}
.app-entry{font-size:7px;font-weight:700;color:var(--ink)}
.app-cols{display:flex;gap:8px;margin-top:16px}
.app-col{flex:1;border:1px solid var(--line);border-radius:3px;padding:3px;height:190px}
.app-col .ct{font-size:5px;color:var(--ink);margin-bottom:6px}
.bar{height:3px;background:#c9d0da;border-radius:2px;margin:3px 2px}
.laptop-base{left:320px;top:752px;width:553px;height:18px;background:linear-gradient(180deg,#c7cbd1,#7d8289);border-radius:2px 2px 12px 12px}

/* why */
.sec-title{left:0;width:1200px;text-align:center;font-size:46px;font-weight:700}
.why-text{left:195px;width:810px;top:994px;text-align:center;font-size:11.5px;line-height:17.5px;color:var(--ink)}
.why-text b{font-weight:700}
.shot{left:192px;top:1102px;width:472px;height:298px;background:#fff;border:2px solid #dde6f1;border-radius:8px;box-shadow:0 6px 20px rgba(20,40,80,.08);overflow:hidden}
.shot .dots{height:18px;background:#f3f5f8;display:flex;gap:6px;align-items:center;padding-left:10px}
.shot .dots i{width:6px;height:6px;border-radius:50%;display:block}
.shot .app{height:calc(100% - 18px)}
.shot .app-bar{width:20px}
.shot .app-col{height:210px}
.feat{left:720px;width:320px}
.feat .chk{position:absolute;left:0;top:6px;width:34px;height:34px;border-radius:50%;background:var(--green);display:flex;align-items:center;justify-content:center}
.feat h3{margin-left:65px;font-size:15px;font-weight:600}
.feat p{margin-left:65px;margin-top:6px;font-size:11px;line-height:17px;color:var(--text)}

/* how */
.step{position:absolute;width:175px;border-radius:88px;background:#e8eef6;text-align:center}
.step .circ{width:148px;height:148px;border-radius:50%;background:#fff;margin:13px auto 0;box-shadow:0 6px 18px rgba(20,40,80,.08);display:flex;align-items:center;justify-content:center}
.step h3{font-family:"Inter",sans-serif;font-size:14px;font-weight:600;color:var(--blue);margin-top:16px}
.step p{font-size:11.5px;line-height:17.5px;color:var(--ink);margin:10px 22px 0}
.num{position:absolute;font-family:"Rubik",sans-serif;font-weight:700;font-size:40px;color:var(--blue-soft)}

/* ai coach */
.band{left:0;top:2113px;width:1200px;height:424px;background:var(--band);overflow:hidden}
.ai-title{left:98px;top:2252px;font-size:46px;line-height:50px;font-weight:700}
.ai-card{left:451px;top:2175px;width:651px;height:308px;background:#fff;border-radius:16px}
.ai-card p{position:absolute;left:55px;top:38px;width:540px;text-align:center;font-size:11.2px;line-height:17.5px;color:var(--ink)}
.coach{position:absolute;width:130px;height:130px;border-radius:50%}
.chip{position:absolute;height:32px;width:138px;border-radius:16px;background:#fff;box-shadow:0 4px 14px rgba(20,40,80,.12);display:flex;align-items:center;gap:8px;padding-left:4px;font-size:11px;color:#9aa3ae}
.chip b{width:36px;height:24px;border-radius:12px;background:var(--blue);color:#fff;font-size:10px;font-weight:600;display:flex;align-items:center;justify-content:center}

/* testimonials */
.tcard{position:absolute;top:2730px;width:267px;height:219px;background:#fff;border-radius:8px;padding:28px 20px 0}
.q{font-family:"Rubik",sans-serif;font-weight:800;font-size:22px;color:var(--ink);line-height:12px;height:14px}
.rate{display:flex;align-items:center;gap:14px;margin-top:8px;font-size:9px;color:var(--text)}
.stars{color:var(--orange);font-size:11px;letter-spacing:1px}
.tcard p{font-size:11.2px;line-height:17.5px;color:var(--ink);margin-top:12px}
.who{display:flex;align-items:center;gap:10px;margin-top:14px;font-size:11px;font-weight:600;color:var(--ink)}
.who i{width:20px;height:20px;border-radius:50%;display:block}

/* download */
.cap-title{left:0;width:1200px;top:3108px;text-align:center;font-family:"Inter",sans-serif;font-size:21px;font-weight:600;color:var(--ink)}
.cap-text{left:0;width:1200px;top:3152px;text-align:center;font-size:12.5px;line-height:15px;color:var(--ink)}
.badge{position:absolute;top:3222px;height:38px;background:#0d0f12;border-radius:6px;border:1px solid #888}

/* footer */
.foot-logo{left:189px;top:3361px;display:flex;align-items:center;gap:10px;font-family:"Rubik",sans-serif;font-weight:700;font-size:21px;color:var(--ink)}
.foot-about{left:189px;top:3405px;width:230px;font-size:11px;line-height:17px;color:var(--muted)}
.lang{left:189px;top:3482px;font-size:10px;color:var(--muted);display:flex;gap:10px;align-items:center}
.lang b{color:var(--ink);font-weight:600}
.fcol h4{font-size:13px;font-weight:500;color:var(--ink);margin-bottom:22px}
.links{display:grid;grid-template-columns:114px 114px;row-gap:14px;font-size:11px;color:var(--muted)}
.socials{display:flex;gap:16px;margin-bottom:18px}
.socials i{width:10px;height:10px;border-radius:50%;background:var(--ink);display:block}
.access{font-size:11px;color:var(--muted);display:flex;gap:8px;align-items:center}
.access i{width:9px;height:9px;border-radius:50%;background:var(--ink);display:block}
.rule{left:189px;top:3526px;width:822px;height:1px;background:var(--line)}
.legal{left:189px;top:3541px;font-size:10px;color:var(--muted);display:flex;gap:12px}
.copy{left:800px;top:3541px;width:211px;text-align:right;font-size:10px;color:var(--muted)}
</style>
</head>
<body>

<section class="hero">
  <div class="glow" style="left:760px;top:300px;width:380px;height:300px;background:#cfe0f4"></div>
  <div class="glow" style="left:60px;top:380px;width:300px;height:240px;background:#d9e6f5"></div>
</section>

<header>
  <div class="abs nav-logo"><span class="logo-dot"></span>Zestora</div>
  <nav class="abs nav-links"><span>Demo</span><span class="sep">/</span><span>Community</span><span class="sep">/</span><span>Pricing</span><span class="sep">/</span><span>Enterprise</span></nav>
  <div class="abs btn-outline">Contact Sales</div>
</header>

<div class="abs hero-kicker">From Reflection to Action:</div>
<h1 class="abs hero-title"><span class="hl">Transform</span> Your<br>Journaling <span class="hl">Experience</span></h1>
<p class="abs hero-sub">Organize your thoughts, track your progress, and gain insights with<br>a journal designed for personal growth</p>
<div class="abs btn-dark">Start Your Journey
  <svg width="18" height="12" viewBox="0 0 18 12"><path d="M1 6h15M11 1l5 5-5 5" fill="none" stroke="#fff" stroke-width="1.6"/></svg></div>

<!-- community avatars -->
<div class="avatar" role="img" aria-label="Smiling user portrait" style="left:222px;top:375px;width:90px;height:90px;background:linear-gradient(135deg,#c9a58b,#5c7fa6)"></div>
<div class="avatar" role="img" aria-label="User portrait" style="left:149px;top:473px;width:60px;height:60px;background:linear-gradient(135deg,#e3c9a8,#9a8070)"></div>
<div class="avatar" style="left:247px;top:491px;width:70px;height:70px;background:var(--orange)" role="img" aria-label="Journal folder icon"></div>
<div class="avatar" role="img" aria-label="User portrait" style="left:324px;top:483px;width:18px;height:18px;border-width:1px;background:#3b3b40"></div>
<div class="avatar" role="img" aria-label="User portrait" style="left:200px;top:565px;width:44px;height:44px;background:linear-gradient(135deg,#8aa0b8,#3b4656)"></div>
<div class="avatar" role="img" aria-label="User portrait" style="left:309px;top:559px;width:52px;height:52px;background:linear-gradient(135deg,#d0d0d0,#555)"></div>
<div class="avatar" role="img" aria-label="User portrait" style="left:271px;top:611px;width:40px;height:40px;background:linear-gradient(135deg,#9db3c6,#6b5a4a)"></div>

<div class="avatar" role="img" aria-label="User portrait" style="left:925px;top:352px;width:62px;height:62px;background:linear-gradient(135deg,#e5e0d6,#5a3c2c)"></div>
<div class="avatar" role="img" aria-label="User portrait" style="left:1013px;top:416px;width:18px;height:18px;border-width:1px;background:#8c6a54"></div>
<div class="avatar" style="left:840px;top:411px;width:72px;height:72px;background:#20b97a;box-shadow:0 0 0 5px #a8e6c8" role="img" aria-label="Lightbulb insight icon"></div>
<div class="avatar" role="img" aria-label="User portrait" style="left:976px;top:475px;width:70px;height:70px;background:linear-gradient(135deg,#e9c9a0,#7a5b46)"></div>
<div class="avatar" role="img" aria-label="User portrait" style="left:872px;top:503px;width:56px;height:56px;background:linear-gradient(135deg,#6f8a5c,#3a2c22)"></div>
<div class="avatar" role="img" aria-label="User portrait" style="left:953px;top:548px;width:22px;height:22px;border-width:2px;background:#6a79c9"></div>
<div class="avatar" role="img" aria-label="User portrait" style="left:832px;top:567px;width:74px;height:74px;background:linear-gradient(135deg,#b7c1cb,#3c3430)"></div>
<div class="avatar" role="img" aria-label="User portrait" style="left:1055px;top:541px;width:36px;height:36px;background:linear-gradient(135deg,#c7a68d,#44414a)"></div>
<div class="avatar" role="img" aria-label="User portrait" style="left:981px;top:583px;width:52px;height:52px;background:linear-gradient(135deg,#d4ebe6,#7a6a58)"></div>

<!-- laptop -->
<div class="abs laptop-screen">
  <div class="app">
    <div class="app-bar"></div>
    <div class="app-main">
      <div class="app-top"></div>
      <div class="app-entry">Entry</div>
      <div class="app-cols">
        <div class="app-col"><div class="ct">What Went Well?</div><div class="bar"></div><div class="bar" style="width:70%"></div><div class="bar"></div><div class="bar" style="width:60%"></div></div>
        <div class="app-col"><div class="ct">What Didn't Go Well?</div><div class="bar"></div><div class="bar" style="width:80%"></div><div class="bar"></div><div class="bar" style="width:50%"></div></div>
        <div class="app-col"><div class="ct">Things To Try</div><div class="bar"></div><div class="bar"></div><div class="bar" style="width:75%"></div><div class="bar"></div><div class="bar" style="width:55%"></div></div>
      </div>
    </div>
  </div>
</div>
<div class="abs laptop-base"></div>

<!-- why choose us -->
<h2 class="abs sec-title" style="top:914px">Why Choose Us?</h2>
<p class="abs why-text"><b>Discover</b> a journaling experience tailored to help you grow. Our app's <b>unique retrospective</b> board format encourages thoughtful reflection, while the upcoming AI coach provides personalized insights to guide your journey. With a user-friendly design and powerful tracking features, our app makes it easy to stay <b>organized</b>, <b>focused</b>, and <b>committed</b> to your personal development.</p>

<div class="abs shot">
  <div class="dots"><i style="background:#f25c54"></i><i style="background:#f5b82e"></i><i style="background:#39c06b"></i></div>
  <div class="app">
    <div class="app-bar"></div>
    <div class="app-main" style="padding:12px 16px">
      <div class="app-entry" style="margin-top:4px">Entry</div>
      <div class="app-cols" style="gap:16px;margin-top:24px">
        <div class="app-col"><div class="ct">What Went Well?</div><div class="bar"></div><div class="bar" style="width:70%"></div><div class="bar"></div><div class="bar" style="width:60%"></div></div>
        <div class="app-col"><div class="ct">What Didn't Go Well?</div><div class="bar"></div><div class="bar" style="width:80%"></div><div class="bar"></div><div class="bar" style="width:50%"></div></div>
        <div class="app-col"><div class="ct">Things To Try</div><div class="bar"></div><div class="bar"></div><div class="bar" style="width:75%"></div><div class="bar"></div><div class="bar" style="width:55%"></div></div>
      </div>
    </div>
  </div>
</div>

<div class="abs feat" style="top:1092px"><span class="chk"><svg width="16" height="12" viewBox="0 0 16 12"><path d="M1.5 6l4.5 4.5L14.5 1.5" fill="none" stroke="#fff" stroke-width="2.6"/></svg></span><h3>Retrospective Board Format</h3><p>Reflect on your experiences with our unique<br>three-part journal structure.</p></div>
<div class="abs feat" style="top:1180px"><span class="chk"><svg width="16" height="12" viewBox="0 0 16 12"><path d="M1.5 6l4.5 4.5L14.5 1.5" fill="none" stroke="#fff" stroke-width="2.6"/></svg></span><h3>AI-Powered Insights</h3><p>Get personalized insights based on your<br>journal history with our upcoming AI coach.</p></div>
<div class="abs feat" style="top:1268px"><span class="chk"><svg width="16" height="12" viewBox="0 0 16 12"><path d="M1.5 6l4.5 4.5L14.5 1.5" fill="none" stroke="#fff" stroke-width="2.6"/></svg></span><h3>Track Progress</h3><p>Monitor your growth over time with easy-to-<br>read summaries.</p></div>
<div class="abs feat" style="top:1356px"><span class="chk"><svg width="16" height="12" viewBox="0 0 16 12"><path d="M1.5 6l4.5 4.5L14.5 1.5" fill="none" stroke="#fff" stroke-width="2.6"/></svg></span><h3>User-Friendly Design</h3><p>Enjoy a clean, intuitive interface that makes<br>journaling a breeze.</p></div>

<!-- how does it work -->
<h2 class="abs sec-title" style="top:1497px">How does it work?</h2>
<svg class="abs" style="left:270px;top:1590px" width="680" height="460" viewBox="0 0 680 460">
  <g fill="none" stroke="#5b8fd6" stroke-width="1.2" stroke-dasharray="4 4">
    <path d="M13 190 V120 A107 107 0 0 1 230 110 V230"/>
    <path d="M230 230 V330 A110 110 0 0 0 450 330 V210"/>
    <path d="M450 200 V120 A108 108 0 0 1 667 110 V190"/>
  </g>
  <circle cx="13" cy="192" r="7" fill="#1460c9"/>
  <circle cx="668" cy="192" r="7" fill="#1460c9"/>
  <path d="M124 8l9 5-9 5z" fill="#1460c9"/>
  <path d="M558 8l9 5-9 5z" fill="#1460c9"/>
  <path d="M225 202l5 9 5-9z" fill="#1460c9"/>
  <path d="M445 209l5-9 5 9z" fill="#1460c9"/>
</svg>

<div class="step" style="left:305px;top:1622px;height:333px">
  <div class="circ"><div role="img" aria-label="Writing on a journal page illustration" style="width:64px;height:58px;border-radius:8px;background:linear-gradient(135deg,#e9574a,#2f7dd3)"></div></div>
  <h3>Start Journaling</h3>
  <p>Create entries by reflecting on what went well, what didn't, and what to try next.</p>
</div>
<div class="num" style="left:367px;top:1980px">01</div>

<div class="step" style="left:524px;top:1690px;height:330px">
  <div class="circ"><div role="img" aria-label="Sticky note illustration" style="width:50px;height:54px;border-radius:4px;background:linear-gradient(135deg,#f5c23a,#e79a12)"></div></div>
  <h3>Price Estimate</h3>
  <p>Keep your ideas and reflections organized in a clear, structured format.</p>
</div>
<div class="num" style="left:584px;top:1614px">02</div>

<div class="step" style="left:743px;top:1622px;height:323px">
  <div class="circ"><div role="img" aria-label="Lightbulb illustration" style="width:44px;height:60px;border-radius:22px 22px 10px 10px;background:linear-gradient(180deg,#f7b928,#444)"></div></div>
  <h3 style="margin-top:10px">Unlock Insights</h3>
  <p>Soon, our AI coach will provide you with valuable feedback and tips based on your entries.</p>
</div>
<div class="num" style="left:802px;top:1973px">03</div>

<!-- ai coach -->
<section class="abs band">
  <div style="position:absolute;left:-60px;top:-40px;width:380px;height:260px;border-radius:50%;background:#d4e2f3;filter:blur(40px)"></div>
</section>
<h2 class="abs ai-title">Your<br>Personal AI<br>Coach</h2>
<svg class="abs" style="left:432px;top:2430px" width="80" height="72" viewBox="0 0 80 72">
  <g fill="#1460c9">
    <circle cx="2" cy="2" r="1.6"/><circle cx="2" cy="10" r="1.6"/><circle cx="2" cy="18" r="1.6"/><circle cx="2" cy="26" r="1.6"/><circle cx="2" cy="34" r="1.6"/><circle cx="2" cy="42" r="1.6"/><circle cx="2" cy="50" r="1.6"/><circle cx="2" cy="58" r="1.6"/><circle cx="2" cy="66" r="1.6"/>
    <circle cx="10" cy="10" r="1.6"/><circle cx="10" cy="26" r="1.6"/><circle cx="10" cy="42" r="1.6"/><circle cx="10" cy="58" r="1.6"/><circle cx="10" cy="66" r="1.6"/>
    <circle cx="18" cy="58" r="1.6"/><circle cx="18" cy="66" r="1.6"/><circle cx="26" cy="58" r="1.6"/><circle cx="26" cy="66" r="1.6"/><circle cx="34" cy="58" r="1.6"/><circle cx="34" cy="66" r="1.6"/><circle cx="42" cy="58" r="1.6"/><circle cx="42" cy="66" r="1.6"/><circle cx="50" cy="58" r="1.6"/><circle cx="50" cy="66" r="1.6"/><circle cx="58" cy="58" r="1.6"/><circle cx="58" cy="66" r="1.6"/><circle cx="66" cy="66" r="1.6"/><circle cx="74" cy="66" r="1.6"/>
  </g>
</svg>
<div class="abs ai-card">
  <p>Briefly explain the upcoming feature. Get ready for the next level of journaling with our AI Coach, coming soon! This smart feature will analyze your journal entries to offer personalized insights, tips, and recommendations. Whether you're reflecting on past experiences or planning future goals, the AI Coach will be your guide, helping you grow faster and more effectively.</p>
  <div class="coach" role="img" aria-label="AI coach portrait, man in suit on orange backdrop" style="left:67px;top:131px;background:linear-gradient(135deg,#f7b12a,#2b3140);border:4px solid #fff;box-shadow:0 0 0 2px #f3d9a6"></div>
  <div class="chip" style="left:167px;top:188px"><b>Ret</b>Your AI Coach</div>
  <div class="coach" role="img" aria-label="AI coach portrait, woman in suit on green backdrop" style="left:351px;top:131px;background:linear-gradient(135deg,#36c583,#1f2a3a);border:4px solid #fff;box-shadow:0 0 0 2px #bfead4"></div>
  <div class="chip" style="left:452px;top:188px"><b>Efy</b>Your AI Coach</div>
</div>

<!-- testimonials -->
<h2 class="abs sec-title" style="top:2633px">What Our Users Are Saying</h2>
<div class="tcard" style="left:189px">
  <div class="q">"</div>
  <div class="rate"><span class="stars">★★★★★</span>4.8 out of 5.0</div>
  <p>This app has completely transformed the way I reflect on my days. The three-part structure makes it so easy to identify patterns in my behavior.</p>
  <div class="who"><i role="img" aria-label="Reviewer avatar" style="background:#e0a14a"></i>Jeanny G. Doe</div>
</div>
<div class="tcard" style="left:466px">
  <div class="q">"</div>
  <div class="rate"><span class="stars">★★★★★</span>4.8 out of 5.0</div>
  <p>I've tried many journaling apps, but this one stands out. The AI insights feature is a game-changer, offering advice that feels personalized and relevant.</p>
  <div class="who"><i role="img" aria-label="Reviewer avatar" style="background:#c6463a"></i>Albert F. Johansen</div>
</div>
<div class="tcard" style="left:744px">
  <div class="q">"</div>
  <div class="rate"><span class="stars">★★★★★</span>4.8 out of 5.0</div>
  <p>Journaling used to feel like a chore, but with this app, it's become a habit I actually look forward to. It's simple, effective, and helps me stay focused on my goals.</p>
  <div class="who"><i role="img" aria-label="Reviewer avatar" style="background:#5e7fa8"></i>Sarah M. Witcwicky</div>
</div>
<svg class="abs" style="left:570px;top:2979px" width="60" height="8" viewBox="0 0 60 8">
  <circle cx="4" cy="4" r="2.5" fill="#c9d6e8"/><rect x="12" y="1.5" width="26" height="5" rx="2.5" fill="#1460c9"/><circle cx="46" cy="4" r="2.5" fill="#c9d6e8"/><circle cx="56" cy="4" r="2.5" fill="#c9d6e8"/>
</svg>

<!-- download -->
<h2 class="abs cap-title">Capture life's moments, anytime, anywhere.</h2>
<p class="abs cap-text">Download the free Zestora journal app for free on phones, tablets and desktops. Or access your Zestora<br>Journal from any browser.</p>
<div class="badge" style="left:390px;width:126px"></div>
<div class="badge" style="left:526px;width:120px"></div>
<div class="badge" style="left:656px;width:154px"></div>

<!-- footer -->
<footer>
  <div class="abs foot-logo"><span class="logo-dot"></span>Zestora</div>
  <p class="abs foot-about">Our journal app helps you reflect, grow, and stay organized with a unique retrospective board format.</p>
  <div class="abs lang">Language <b>ENG</b><svg width="10" height="6" viewBox="0 0 10 6"><path d="M1 1l4 4 4-4" fill="none" stroke="#16181d" stroke-width="1.4"/></svg></div>
  <div class="abs fcol" style="left:503px;top:3361px">
    <h4>Links</h4>
    <div class="links"><span>About Us</span><span>Integrations</span><span>Contact Us</span><span>Pricing</span><span>Enterprise</span><span>Template</span><span>Contact Sales</span><span>24/7 Support</span></div>
  </div>
  <div class="abs fcol" style="left:797px;top:3361px">
    <h4>Connect with Us</h4>
    <div class="socials"><i></i><i></i><i></i><i></i><i></i></div>
    <div class="access"><i></i>Accessibility Statement</div>
  </div>
  <div class="abs rule"></div>
  <div class="abs legal"><span>Terms &amp; Conditions</span><span>|</span><span>Privacy Policy</span><span>|</span><span>Refund Policy</span></div>
  <div class="abs copy">© 2024 —Zestora.com. All Rights Reserved.</div>
</footer>

</body>
</html>
```